Business card design for my company.
I would like the card's background colour to be black. You can also see our web site to get an idea of our brand. https://www.tmwhomecrafting.com.au/
- Name
- Email

```html
<!DOCTYPE html>
<html lang="en">
<head>
<meta charset="utf-8">
<title>TMW Home Crafting – Business Card</title>
<link rel="stylesheet" href="https://fonts.googleapis.com/css2?family=Montserrat:wght@500;700&family=Poppins:wght@400&display=swap">
<style>
  :root {
    --backdrop: #2b2a2f;
    --card: #1f2123;
    --brand-green: #1f9a48;
    --ink-white: #f2f2f2;
    --shadow: rgba(0, 0, 0, 0.45);
  }
  * { margin: 0; padding: 0; box-sizing: border-box; }
  html, body { width: 1200px; height: 801px; overflow: hidden; }
  body {
    background: var(--backdrop);
    display: flex;
    align-items: center;
    justify-content: center;
    gap: 60px;
  }
  .card {
    width: 520px;
    height: 297px;
    background: var(--card);
    box-shadow: 0 18px 40px var(--shadow);
    position: relative;
  }
  /* Front */
  .card-front {
    display: flex;
    align-items: center;
    justify-content: center;
  }
  .wordmark {
    display: flex;
    align-items: center;
    gap: 14px;
    font-family: "Montserrat", sans-serif;
    font-weight: 700;
    font-size: 30px;
    letter-spacing: 3px;
    color: var(--ink-white);
    text-transform: uppercase;
  }
  .wordmark-dot {
    width: 18px;
    height: 18px;
    border-radius: 50%;
    background: var(--brand-green);
  }
  /* Back */
  .card-back {
    display: flex;
    align-items: center;
    padding: 0 36px 0 56px;
  }
  .identity {
    font-family: "Montserrat", sans-serif;
    text-transform: uppercase;
  }
  .identity-name {
    color: var(--brand-green);
    font-weight: 700;
    font-size: 25px;
    letter-spacing: 0.5px;
    line-height: 1.1;
  }
  .identity-role {
    color: var(--ink-white);
    font-weight: 500;
    font-size: 13px;
    letter-spacing: 1px;
    margin-top: 4px;
  }
  .divider {
    width: 1.5px;
    height: 70px;
    background: var(--ink-white);
    margin: 0 22px;
  }
  .contact-list {
    list-style: none;
    font-family: "Poppins", sans-serif;
    font-size: 13px;
    color: var(--ink-white);
  }
  .contact-item {
    display: flex;
    align-items: center;
    gap: 9px;
    line-height: 1.85;
  }
  .contact-icon {
    width: 16px;
    height: 16px;
    flex: none;
  }
</style>
</head>
<body>
  <section class="card card-front" aria-label="Business card front">
    <div class="wordmark">
      <span class="wordmark-dot"></span>
      <span class="wordmark-name">TMW Home Crafting</span>
    </div>
  </section>

  <section class="card card-back" aria-label="Business card back">
    <div class="identity">
      <p class="identity-name">Dean Hartley</p>
      <p class="identity-role">General Manager</p>
    </div>
    <span class="divider"></span>
    <ul class="contact-list">
      <li class="contact-item">
        <svg class="contact-icon" viewBox="0 0 16 16" aria-hidden="true">
          <circle cx="8" cy="8" r="8" fill="var(--brand-green)"/>
          <rect x="5.5" y="3.5" width="5" height="9" rx="1" fill="none" stroke="#fff" stroke-width="1.2"/>
        </svg>
        <span>0400 123 456</span>
      </li>
      <li class="contact-item">
        <svg class="contact-icon" viewBox="0 0 16 16" aria-hidden="true">
          <circle cx="8" cy="8" r="8" fill="var(--brand-green)"/>
          <rect x="4" y="5" width="8" height="6" fill="none" stroke="#fff" stroke-width="1.1"/>
          <path d="M4 5 L8 8.5 L12 5" fill="none" stroke="#fff" stroke-width="1.1"/>
        </svg>
        <span>info@tmwhomecrafting.com.au</span>
      </li>
      <li class="contact-item">
        <svg class="contact-icon" viewBox="0 0 16 16" aria-hidden="true">
          <circle cx="8" cy="8" r="8" fill="var(--brand-green)"/>
          <circle cx="8" cy="8" r="4.2" fill="none" stroke="#fff" stroke-width="1"/>
          <ellipse cx="8" cy="8" rx="1.8" ry="4.2" fill="none" stroke="#fff" stroke-width="0.9"/>
          <path d="M3.8 8 H12.2" stroke="#fff" stroke-width="0.9"/>
        </svg>
        <span>www.tmwhomecrafting.com.au</span>
      </li>
    </ul>
  </section>
</body>
</html>
```